BRISKLY sparkling water needs new artwork! Based in Southern California

"Briskly" is a new sparkling water company based in Southern California that offers refreshing flavors (lime, cherry, & mango) with B vitamins and antioxidants.

We would like to see packaging designs for standard 12oz cans for each of the three flavors.
Our initial preference is to have individual artwork for each flavor.

Attached are examples of competitors' designs.
Updates

We are extending the deadline for the Thanksgiving Holiday. Thank you all for your contributions.

```html
<!DOCTYPE html>
<html lang="en">
<head>
<meta charset="utf-8">
<title>Briskly Sparkling Water – 12oz Can Labels</title>
<link href="https://fonts.googleapis.com/css2?family=Lexend:wght@500;600&family=Michroma&family=PT+Sans:wght@400;700&family=Roboto+Condensed:ital,wght@0,400;0,700;1,700&display=swap" rel="stylesheet">
<style>
  :root {
    --guide: #9c88c6;
    --guide-line: #b8a9d9;
    --ink: #1c1c1c;
    --paper: #ffffff;
  }
  html, body { margin: 0; padding: 0; width: 1200px; height: 2382px; overflow: hidden; background: var(--paper); }
  .sheet { display: block; width: 1200px; height: 2382px; }

  .cherry { --main: #e0004d; --tint: #fdf1f3; --w1: #f4aab5; --w2: #e8566f; --w3: #e0004d; --w4: #a6003a; --w5: #e3064f; }
  .lime   { --main: #5aa513; --tint: #f6fbe6; --w1: #5fa818; --w2: #4c8c0f; --w3: #7dbd0a; --w4: #4a8a10; --w5: #6fb10d; }
  .mango  { --main: #f39a12; --tint: #fbfce3; --w1: #ffe04a; --w2: #f7c300; --w3: #ffe451; --w4: #f5bd00; --w5: #ffdf3a; }

  .template-title { font-family: "PT Sans", sans-serif; font-size: 28px; fill: var(--guide); text-anchor: middle; }
  .guide-note { font-family: "PT Sans", sans-serif; font-size: 12px; fill: var(--guide); }
  .guide-small { font-family: "PT Sans", sans-serif; font-size: 9.5px; fill: var(--guide); text-anchor: middle; }
  .guide-strong { font-family: "Roboto Condensed", sans-serif; font-weight: 700; font-size: 14px; fill: var(--guide); }
  .guide-sub { font-family: "Roboto Condensed", sans-serif; font-size: 9.5px; fill: var(--guide); }
  .dim-text { font-family: "Roboto Condensed", sans-serif; font-size: 13px; fill: var(--guide); text-anchor: middle; }
  .guide-line { stroke: var(--guide-line); stroke-width: 1; fill: none; }
  .guide-dash { stroke: var(--guide); stroke-width: 1; stroke-dasharray: 7 5; fill: none; }
  .lf-frame { stroke: var(--guide); stroke-width: 1.2; fill: none; }

  .label-bg { fill: var(--tint); }
  .cherry .fruit-art { fill: url(#artCherry); }
  .lime .fruit-art { fill: url(#artLime); }
  .mango .fruit-art { fill: url(#artMango); }
  .wave-1 { fill: var(--w1); } .wave-2 { fill: var(--w2); } .wave-3 { fill: var(--w3); }
  .wave-4 { fill: var(--w4); } .wave-5 { fill: var(--w5); }
  .bleed-strip { fill: var(--w4); }

  .brand-name { font-family: "Lexend", sans-serif; font-weight: 600; font-size: 60px; fill: var(--main); text-anchor: middle; letter-spacing: 1px; }
  .product-line { font-family: "Michroma", sans-serif; font-size: 24px; fill: var(--ink); text-anchor: middle; }
  .rule { fill: var(--main); }
  .claims { font-family: "PT Sans", sans-serif; font-size: 12.5px; fill: var(--ink); text-anchor: middle; }
  .flavor-pill { fill: var(--main); }
  .flavor-name { font-family: "Lexend", sans-serif; font-weight: 600; font-size: 13px; fill: #fff; text-anchor: middle; letter-spacing: 2.5px; }
  .size { font-family: "Lexend", sans-serif; font-weight: 500; font-size: 19px; fill: #fff; text-anchor: middle; }
  .mango .size { fill: #6b4a00; }

  .badge { fill: #fff; stroke: var(--main); stroke-width: 2; }
  .badge-num { font-family: "Roboto Condensed", sans-serif; font-weight: 700; font-size: 11px; fill: var(--main); text-anchor: middle; }
  .badge-txt { font-family: "Roboto Condensed", sans-serif; font-size: 4.5px; fill: var(--main); text-anchor: middle; }
  .bubble { fill: none; stroke: var(--main); stroke-width: 0.8; opacity: 0.6; }

  .info-box { fill: #fff; stroke: #444; stroke-width: 1; }
  .info-label { font-family: "PT Sans", sans-serif; font-weight: 700; font-size: 8px; fill: var(--ink); text-anchor: middle; }

  .seal { fill: #fff; stroke: var(--main); stroke-width: 4; }
  .seal-ring { fill: none; stroke: var(--main); stroke-width: 1; }
  .seal-text { font-family: "Roboto Condensed", sans-serif; font-style: italic; font-weight: 700; font-size: 13px; fill: var(--main); text-anchor: middle; }
</style>
</head>
<body>
<svg class="sheet" viewBox="0 0 1300 2580" xmlns="http://www.w3.org/2000/svg">
  <defs>
    <linearGradient id="artCherry" x1="0" y1="0" x2="0" y2="1">
      <stop offset="0" stop-color="#f7c6cf" stop-opacity="0.75"/>
      <stop offset="1" stop-color="#fbe1e6" stop-opacity="0.5"/>
    </linearGradient>
    <linearGradient id="artLime" x1="0" y1="0" x2="0" y2="1">
      <stop offset="0" stop-color="#d9ef9f" stop-opacity="0.8"/>
      <stop offset="1" stop-color="#ecf7cc" stop-opacity="0.5"/>
    </linearGradient>
    <linearGradient id="artMango" x1="0" y1="0" x2="0" y2="1">
      <stop offset="0" stop-color="#ffe27a" stop-opacity="0.8"/>
      <stop offset="1" stop-color="#fff3b5" stop-opacity="0.5"/>
    </linearGradient>

    <g id="guides">
      <line class="guide-line" x1="199" y1="172" x2="199" y2="225"/>
      <line class="guide-dash" x1="205" y1="172" x2="205" y2="760"/>
      <line class="guide-dash" x1="1067" y1="172" x2="1067" y2="760"/>
      <line class="guide-line" x1="1089" y1="172" x2="1089" y2="225"/>
      <line class="guide-line" x1="120" y1="237" x2="170" y2="237"/>
      <line class="guide-line" x1="120" y1="244" x2="170" y2="244"/>
      <line class="guide-line" x1="1105" y1="237" x2="1155" y2="237"/>
      <line class="guide-line" x1="1105" y1="244" x2="1155" y2="244"/>
      <line class="guide-line" x1="122" y1="720" x2="172" y2="720"/>
      <line class="guide-line" x1="122" y1="727" x2="172" y2="727"/>
      <line class="guide-line" x1="1110" y1="720" x2="1160" y2="720"/>
      <line class="guide-line" x1="1110" y1="727" x2="1160" y2="727"/>
      <rect class="guide-line" x="197" y="237" width="893" height="490"/>
      <rect class="guide-line" x="205" y="244" width="862" height="476"/>
      <line class="guide-dash" x1="172" y1="293" x2="1115" y2="293"/>
      <rect class="lf-frame" x="427" y="196" width="433" height="544"/>
      <line class="guide-line" x1="203" y1="756" x2="568" y2="756"/>
      <line class="guide-line" x1="705" y1="756" x2="1088" y2="756"/>
      <line class="guide-line" x1="203" y1="742" x2="203" y2="776"/>
      <line class="guide-line" x1="1088" y1="742" x2="1088" y2="776"/>
      <line class="guide-line" x1="1125" y1="187" x2="1082" y2="238"/>
      <circle cx="1125" cy="187" r="3" fill="#9c88c6"/>
    </g>

    <g id="notes">
      <text class="guide-note" x="176" y="164">1 mm clear</text>
      <text class="guide-note" x="1047" y="164">5 mm clear</text>
      <text class="guide-strong" x="1115" y="166">Transitional Area</text>
      <text class="guide-sub" x="1115" y="178">(transitions from sidewall to neck)</text>
      <text class="guide-note" x="622" y="184">109 mm LF</text>
      <text class="guide-note" x="50" y="246">2 mm clear</text>
      <text class="guide-note" x="1162" y="246">2 mm clear</text>
      <text class="guide-note" x="52" y="727">2 mm clear</text>
      <text class="guide-note" x="1167" y="727">2 mm clear</text>
      <text class="guide-note" x="1110" y="464">4.875″ Cut Height</text>
      <text class="guide-note" x="1110" y="481">123.825 MM</text>
      <text class="dim-text" x="633" y="760">225 MM SLIT WIDTH</text>
      <text class="dim-text" x="633" y="775">8.8583″</text>
      <text class="guide-small" x="231" y="800">1mm Bkgd Bleed</text>
      <text class="guide-small" x="231" y="812">Overlap</text>
      <text class="guide-small" x="1008" y="782">2mm Bkgd Only</text>
      <text class="guide-small" x="1008" y="794">No Text/Art</text>
    </g>

    <g id="waves">
      <rect class="bleed-strip" x="427" y="727" width="433" height="13"/>
      <path class="wave-1" d="M197,595 C290,570 380,612 480,590 S680,565 790,590 S990,615 1090,582 V727 H197 Z"/>
      <path class="wave-2" d="M197,612 C300,592 400,625 510,606 S720,588 830,608 S1000,622 1090,602 V727 H197 Z"/>
      <path class="wave-3" d="M197,640 C290,622 410,652 520,632 S730,615 840,638 S1010,650 1090,630 V727 H197 Z"/>
      <path class="wave-4" d="M197,665 C300,650 400,678 520,660 S720,645 830,665 S1010,678 1090,658 V727 H197 Z"/>
      <path class="wave-5" d="M197,690 C300,676 410,700 520,686 S730,672 840,690 S1010,700 1090,684 V727 H197 Z"/>
    </g>

    <g id="sidePanel">
      <circle class="badge" cx="375" cy="337" r="15"/><text class="badge-num" x="375" y="339">0</text><text class="badge-txt" x="375" y="346">SUGAR</text>
      <circle class="badge" cx="375" cy="373" r="15"/><text class="badge-num" x="375" y="375">0</text><text class="badge-txt" x="375" y="382">CALORIES</text>
      <circle class="badge" cx="375" cy="409" r="15"/><text class="badge-num" x="375" y="411">0</text><text class="badge-txt" x="375" y="418">SODIUM</text>
      <circle class="badge" cx="375" cy="445" r="15"/><text class="badge-txt" x="375" y="444" style="font-size:6px">B6 &amp;</text><text class="badge-txt" x="375" y="451" style="font-size:6px">B12</text>
      <circle class="badge" cx="375" cy="481" r="15"/><text class="badge-txt" x="375" y="480" style="font-size:6px">NON</text><text class="badge-txt" x="375" y="487" style="font-size:6px">GMO</text>
      <circle class="badge" cx="375" cy="517" r="15"/><text class="badge-txt" x="375" y="525">GLUTEN FREE</text>
      <circle class="badge" cx="375" cy="553" r="15"/><text class="badge-txt" x="375" y="562">VEGAN</text>
      <circle class="bubble" cx="354" cy="394" r="4"/><circle class="bubble" cx="391" cy="466" r="3"/>
      <circle class="bubble" cx="357" cy="535" r="3"/><circle class="bubble" cx="392" cy="574" r="3"/>

      <rect class="info-box" x="875" y="338" width="119" height="167"/>
      <text class="info-label" x="934" y="354">NUTRITION PANEL</text>
      <rect class="info-box" x="1001" y="425" width="56" height="80"/>
      <text class="info-label" transform="translate(1032 465) rotate(-90)">BARCODE</text>

      <circle class="seal" cx="962" cy="550" r="33"/>
      <circle class="seal-ring" cx="962" cy="550" r="27"/>
      <text class="seal-text" x="962" y="547">BOOST</text>
      <text class="seal-text" x="962" y="563">IMMUNITY</text>
      <circle class="bubble" cx="924" cy="575" r="3"/><circle class="bubble" cx="1005" cy="577" r="4"/>
    </g>

    <g id="frontPanel">
      <text class="brand-name" x="635" y="386">briskly</text>
      <text class="product-line" x="635" y="442">SPARKLING</text>
      <text class="product-line" x="635" y="467">WATER</text>
      <rect class="rule" x="610" y="475" width="50" height="2.5"/>
      <text class="claims" x="635" y="500">NATURAL FLAVORS</text>
      <text class="claims" x="635" y="515">&amp; B-VITAMINS</text>
      <rect class="flavor-pill" x="593" y="526" width="85" height="18" rx="9"/>
      <text class="size" x="635" y="705">12oz</text>
    </g>
  </defs>

  <g class="can-template cherry">
    <text class="template-title" x="658" y="124">109 mm LF_4.875″_Template</text>
    <rect class="label-bg" x="197" y="237" width="893" height="490"/>
    <rect class="fruit-art" x="197" y="237" width="893" height="380" role="img" aria-label="Scattered illustrated red cherries with green leaves across the label"/>
    <use href="#waves"/>
    <use href="#sidePanel"/>
    <use href="#frontPanel"/>
    <text class="flavor-name" x="636" y="540">CHERRY</text>
    <use href="#guides"/>
    <use href="#notes"/>
  </g>

  <g class="can-template lime" transform="translate(0 832)">
    <text class="template-title" x="658" y="124">109 mm LF_4.875″_Template</text>
    <rect class="label-bg" x="197" y="237" width="893" height="490"/>
    <rect class="fruit-art" x="197" y="237" width="893" height="380" role="img" aria-label="Scattered illustrated lime slices in light green across the label"/>
    <use href="#waves"/>
    <use href="#sidePanel"/>
    <use href="#frontPanel"/>
    <text class="flavor-name" x="636" y="540">LIME</text>
    <use href="#guides"/>
    <use href="#notes"/>
  </g>

  <g class="can-template mango" transform="translate(0 1658)">
    <text class="template-title" x="658" y="124">109 mm LF_4.875″_Template</text>
    <rect class="label-bg" x="197" y="237" width="893" height="490"/>
    <rect class="fruit-art" x="197" y="237" width="893" height="380" role="img" aria-label="Scattered illustrated whole and cut mangoes with leaves across the label"/>
    <use href="#waves"/>
    <use href="#sidePanel"/>
    <use href="#frontPanel"/>
    <text class="flavor-name" x="636" y="540">MANGO</text>
    <use href="#guides"/>
    <use href="#notes"/>
  </g>
</svg>
</body>
</html>
```